Heron Property Inspection business card

I am the principal inspector of Heron Property Inspections. I serve Northern Virginia from Winchester to Arlington.Associate, Federated Guild of Dwelling Examiners (FGDE)Graduate, FGDE Home Inspectors CourseNational Association of Home Inspectors ExamI'd like the business card to look more professional than comical.I pulled the attached picture off the web. I'd like to have something like that or an image of a house as my logo on the cards.

Target Market(s)

Persons who recently purchased a home.

Industry/Entity Type

Business

Contact Information for Business Card

Bob AllenBadger Home Inspections, LLC.4455 River RoadBluemont, Virginia 20135cell: 703-231-6680e-mail: tkmarlow@postvale.net

Font styles to use
Serif
Sans Serif

Requirements
Must have
• I'd like to have a logo, something that identifies me as a home inspector. The attached images are something that I'd like to have incorporated into my business card logo.
Nice to have
• I'd like a sketch of a house and/or a magnifying glass showing a house being inspected. The attached images are used as a suggestion only, I do not own the images.
Should not have
• Gimmicky stuff. I want to appear professional and trustworthy.

```html
<!DOCTYPE html>
<html lang="en">
<head>
<meta charset="utf-8">
<title>Heron Property Inspections – Business Card</title>
<link rel="stylesheet" href="https://fonts.googleapis.com/css2?family=Open+Sans:wght@400;600&display=swap">
<style>
  :root {
    --page-bg: #e7e5e2;
    --card-top: #ffffff;
    --card-bottom: #d9d9d9;
    --brand-red: #9b1b1e;
    --ink-grey: #4a4b4d;
    --ink-dark: #2b2b2b;
  }
  * { margin: 0; padding: 0; box-sizing: border-box; }
  html, body {
    width: 1200px; height: 892px; overflow: hidden;
    background: var(--page-bg);
    font-family: "Open Sans", Arial, sans-serif;
  }
  .business-card {
    position: absolute;
    left: 130px; top: 176px;
    width: 940px; height: 540px;
    background: linear-gradient(180deg, var(--card-top) 0%, var(--card-top) 30%, var(--card-bottom) 100%);
    box-shadow: 0 10px 30px rgba(0,0,0,0.25);
    overflow: hidden;
  }
  .brand {
    position: absolute;
    left: 120px; top: 56px;
    color: var(--ink-grey);
    font-weight: 600;
    line-height: 1.1;
  }
  .brand__mark {
    display: block;
    width: 96px; height: 96px;
    margin: 0 0 14px 150px;
    background: var(--brand-red);
  }
  .brand__owner { font-size: 40px; letter-spacing: 0.5px; }
  .brand__rule {
    height: 4px; width: 430px;
    background: var(--brand-red);
    margin: 6px 0 6px;
  }
  .brand__company { font-size: 30px; padding-left: 8px; }
  .staff {
    position: absolute;
    left: 140px; top: 318px;
    right: 0;
  }
  .staff__name-row { display: flex; align-items: flex-end; }
  .staff__name {
    color: var(--brand-red);
    font-size: 46px;
    font-weight: 400;
    line-height: 1;
    white-space: nowrap;
  }
  .staff__line {
    flex: 1;
    height: 2px;
    background: var(--brand-red);
    margin: 0 0 2px 14px;
  }
  .staff__title {
    color: var(--ink-dark);
    font-size: 20px;
    margin-top: 4px;
    padding-left: 40px;
  }
  .contacts {
    position: absolute;
    left: 150px; top: 436px;
    list-style: none;
    color: var(--ink-dark);
    font-size: 22px;
  }
  .contacts li {
    display: flex; align-items: center;
    height: 30px;
    white-space: nowrap;
  }
  .contacts svg { width: 20px; height: 20px; margin-right: 14px; flex: none; }
</style>
</head>
<body>
  <div class="business-card">
    <div class="brand">
      <span class="brand__mark" aria-hidden="true"></span>
      <div class="brand__owner">Tim Marlow</div>
      <div class="brand__rule"></div>
      <div class="brand__company">Heron Property Inspections, LLC</div>
    </div>

    <div class="staff">
      <div class="staff__name-row">
        <span class="staff__name">Employee name</span>
        <span class="staff__line"></span>
      </div>
      <div class="staff__title">Managing Director</div>
    </div>

    <ul class="contacts">
      <li>
        <svg viewBox="0 0 20 20" aria-hidden="true"><rect width="20" height="20" rx="4" fill="#9b1b1e"/><rect x="6" y="5" width="8" height="10" rx="1.5" fill="none" stroke="#fff" stroke-width="1.8"/></svg>
        703-555-0192
      </li>
      <li>
        <svg viewBox="0 0 20 20" aria-hidden="true"><rect width="20" height="20" rx="4" fill="#9b1b1e"/><rect x="4.5" y="6" width="11" height="8" fill="none" stroke="#fff" stroke-width="1.5"/><path d="M4.5 6 L10 11 L15.5 6" fill="none" stroke="#fff" stroke-width="1.5"/></svg>
        tkmarlow@postvale.net
      </li>
      <li>
        <svg viewBox="0 0 20 20" aria-hidden="true"><rect width="20" height="20" rx="4" fill="#9b1b1e"/><path d="M10 16 C7 12 6 10.5 6 8.5 A4 4 0 0 1 14 8.5 C14 10.5 13 12 10 16 Z" fill="#fff"/><circle cx="10" cy="8.5" r="1.5" fill="#9b1b1e"/></svg>
        7182 Quarry Lane Fernhill, Virginia 20148
      </li>
    </ul>
  </div>
</body>
</html>
```